Stationary design for boutique production house

We need a stationary design for our production house, 'Lorno Productions' based in Singapore. We produce microfilms as well as podcasts, talkshows and events. Our logo is a stylized icon of our director, who is also the executive producer and host of our programs, Lorno. Our main company colors are Red, Black and white. We would like a clean, minimalist design incorporating our existing company logo that conveys a sense of urbanism and elegance.

Logo and font files are attached. f

Target Market(s)

We focus on lifestyle media rather than entertainment.

Industry/Entity Type

Boutique

Font styles to use
Serif
Sans Serif

Colors
ec1f27
ffffff
000000

Requirements
Must have
• Our company logo and at least one of our company colors.
Nice to have
• Our address and contact information.
Should not have
• Changes made to the company logo (using only certain parts of it is fine though)

```html
<!DOCTYPE html>
<html lang="en">
<head>
<meta charset="utf-8">
<title>Lorno Productions — Stationery</title>
<link rel="stylesheet" href="https://fonts.googleapis.com/css2?family=Libre+Bodoni:wght@400;600&family=Arimo:wght@400&display=swap">
<style>
  :root {
    --red: #ec1f27;
    --red-deep: #b40f16;
    --black: #000000;
    --ink: #1a1a1a;
    --white: #ffffff;
    --paper: #eeeeee;
    --paper-shade: #dcdcdc;
    --backdrop: #e6dcc6;
    --serif: "Libre Bodoni", "Bodoni Moda", Georgia, serif;
    --sans: "Arimo", Arial, sans-serif;
  }
  * { box-sizing: border-box; margin: 0; padding: 0; }
  html, body { width: 1200px; height: 1118px; overflow: hidden; }
  body {
    position: relative;
    background: linear-gradient(160deg, #efe7d6 0%, var(--backdrop) 55%, #d8cbb0 100%);
    font-family: var(--serif);
  }

  /* Letterhead */
  .letterhead {
    position: absolute; left: 512px; top: 170px; width: 549px; height: 778px;
    background: linear-gradient(180deg, #f4f4f4 0%, var(--paper) 60%, var(--paper-shade) 100%);
    box-shadow: 0 3px 6px rgba(0,0,0,.25);
  }
  .letterhead__header {
    position: relative; height: 112px;
    background: linear-gradient(90deg, var(--red-deep) 0%, #d93a44 100%);
    border-bottom: 4px solid var(--ink);
  }
  .letterhead__name {
    position: absolute; left: 60px; top: 30px;
    display: flex; align-items: center; gap: 8px;
    color: var(--white); font-weight: 600; font-size: 17px; letter-spacing: .5px;
  }
  .letterhead__address {
    position: absolute; left: 348px; top: 36px;
    color: var(--white); font-size: 11px; line-height: 14px;
  }
  .letterhead__address .phone { font-family: var(--sans); font-size: 10px; margin-top: 3px; }

  /* Envelope */
  .envelope {
    position: absolute; left: 70px; top: 262px; width: 600px; height: 272px;
    background: linear-gradient(180deg, #e9e9e9 0%, var(--paper) 100%);
    box-shadow: 0 3px 8px rgba(0,0,0,.25);
    overflow: hidden;
  }
  .envelope__flap {
    position: absolute; left: 0; top: 0; width: 100%; height: 52px;
    background: #e2e2e2; border-bottom: 4px solid #7a1418;
  }
  .envelope__brand {
    position: absolute; left: 56px; top: 96px;
    display: flex; align-items: center; gap: 10px;
  }
  .envelope__band {
    position: absolute; left: 0; bottom: 0; width: 100%; height: 46px;
    background: linear-gradient(90deg, var(--red-deep), var(--red));
    border-top: 5px solid var(--ink);
    color: var(--white); font-size: 14px; letter-spacing: .3px;
    display: flex; align-items: center; padding-left: 56px;
  }

  .brand-dot { width: 12px; height: 12px; border-radius: 50%; background: var(--red); flex: none; }
  .brand-name { font-family: var(--serif); font-weight: 400; color: var(--ink); line-height: 1; }
  .envelope .brand-name { font-size: 26px; }

  /* Business card front */
  .card {
    position: absolute; width: 246px; height: 150px;
    box-shadow: 0 2px 5px rgba(0,0,0,.3); overflow: hidden;
  }
  .card--front { left: 210px; top: 616px; background: var(--red-deep); }
  .card--front svg { position: absolute; left: 0; top: 0; }
  .card__brand {
    position: absolute; left: 0; right: 0; top: 44px;
    display: flex; justify-content: center; align-items: center; gap: 6px;
  }
  .card--front .brand-name { font-size: 15px; }
  .card__contact {
    position: absolute; left: 12px; right: 8px; bottom: 12px;
    color: var(--white); font-size: 6.5px; line-height: 10px; text-align: center;
  }
  .card__contact .sans { font-family: var(--sans); }

  /* Business card back */
  .card--back {
    left: 196px; top: 796px; background: var(--black);
    display: flex; justify-content: center; align-items: center; gap: 8px;
  }
  .card--back .brand-name { color: var(--white); font-size: 17px; }
  .card--back .brand-dot { background: var(--white); }
</style>
</head>
<body>

<section class="letterhead" aria-label="Letterhead">
  <header class="letterhead__header">
    <div class="letterhead__name"><span class="brand-dot" style="background:var(--white)"></span>Lorno Productions</div>
    <address class="letterhead__address" style="font-style:normal">
      12 Kallan Lane,<br>
      Meridian Works Building,<br>
      #04 02, Singapore 348210
      <div class="phone">+65 6100 4275</div>
    </address>
  </header>
</section>

<section class="envelope" aria-label="Envelope">
  <div class="envelope__flap"></div>
  <div class="envelope__brand">
    <span class="brand-dot"></span>
    <span class="brand-name">Lorno Productions</span>
  </div>
  <div class="envelope__band">12 Kallan Lane, Meridian Works Building, #04 02, Singapore 348210</div>
</section>

<section class="card card--front" aria-label="Business card front">
  <svg width="246" height="150" viewBox="0 0 246 150" aria-hidden="true">
    <path d="M0 0 H246 V42 C200 120 60 120 0 60 Z" fill="#eeeeee"/>
    <path d="M0 60 C60 120 200 120 246 42 L246 50 C200 132 50 128 0 72 Z" fill="#000"/>
  </svg>
  <div class="card__brand">
    <span class="brand-dot"></span>
    <span class="brand-name">Lorno Productions</span>
  </div>
  <div class="card__contact">
    <div class="sans">+65 6100 4275 &nbsp;|&nbsp; hello@lornoprod.sg</div>
    <div>12 Kallan Lane, Meridian Works Building, #04 02, Singapore 348210</div>
  </div>
</section>

<section class="card card--back" aria-label="Business card back">
  <span class="brand-dot"></span>
  <span class="brand-name">Lorno Productions</span>
</section>

</body>
</html>
```